BOLD & MINIMALIST DESIGN NEEDED

We want a very bold but minimalistic business card design that is impactful and utilizes both sides of the business card. Our current logo is included for your use.

We want bold fonts and good use of negative space. We don't want the logo to overpower the design.

Target Market(s)

Professionals who are building new commercial buildings.

Industry/Entity Type

Construction

Contact Information for Business Card

Name, Title, email, office phone, cell phone, website

Font styles to use
Serif
Sans Serif

Requirements
Must have
• Bold design!

```html
<!DOCTYPE html>
<html lang="en">
<head>
<meta charset="utf-8">
<title>Ridgeline Design + Build – Business Card</title>
<link href="https://fonts.googleapis.com/css2?family=Montserrat:wght@400;500;700;800&display=swap" rel="stylesheet">
<style>
  :root {
    --green: #84c341;
    --ink: #111111;
    --paper: #ffffff;
    --backdrop: #e9ebe6;
    --muted: #2b2b2b;
  }
  * { box-sizing: border-box; margin: 0; padding: 0; }
  html, body {
    width: 1200px; height: 900px; overflow: hidden;
    background: var(--backdrop);
    font-family: "Montserrat", Arial, sans-serif;
  }
  .sheet {
    width: 1200px; height: 900px;
    display: flex; flex-direction: column; align-items: center; justify-content: center;
    gap: 40px;
  }
  .card {
    position: relative;
    width: 680px; height: 388px;
    border-radius: 26px;
    overflow: hidden;
    box-shadow: 0 6px 18px rgba(0,0,0,.12);
  }

  /* Front side */
  .card--front { background: var(--green); }
  .front-mark {
    position: absolute; left: 0; right: 0; top: 0; bottom: 0;
    display: flex; align-items: center; justify-content: center; gap: 28px;
  }
  .front-mark__square { width: 62px; height: 62px; background: var(--paper); }
  .front-mark__name {
    color: var(--paper); font-weight: 800; line-height: 1.05;
    text-transform: uppercase; letter-spacing: .02em;
  }
  .front-mark__name .line1 { display: block; font-size: 66px; }
  .front-mark__name .line2 { display: block; font-size: 31px; letter-spacing: .2em; }

  /* Back side */
  .card--back { background: var(--paper); }
  .back-brand {
    position: absolute; left: 44px; top: 98px; width: 290px;
    color: var(--ink); font-weight: 800; text-transform: uppercase; line-height: 1.05;
  }
  .back-brand .line1 { display: block; font-size: 44px; letter-spacing: .01em; }
  .back-brand .line2 { display: block; font-size: 19px; letter-spacing: .26em; margin-top: 6px; }
  .divider {
    position: absolute; left: 358px; top: 60px; width: 2px; height: 196px;
    background: var(--green);
  }
  .contact { position: absolute; left: 388px; top: 62px; }
  .contact__name {
    color: var(--green); font-weight: 700; font-size: 30px;
    text-transform: uppercase; letter-spacing: .02em;
  }
  .contact__title {
    color: var(--muted); font-size: 15px; font-weight: 500;
    text-transform: uppercase; margin-top: 2px; letter-spacing: .03em;
  }
  .contact__list { list-style: none; margin-top: 18px; }
  .contact__list li {
    display: flex; align-items: center; gap: 10px;
    font-size: 16px; color: var(--muted); margin-bottom: 6px;
  }
  .contact__list svg { width: 15px; height: 15px; flex: none; fill: var(--green); }

  .address-band {
    position: absolute; left: 0; bottom: 44px; width: 520px; height: 38px;
    background: var(--green);
    display: flex; align-items: center; padding-left: 44px;
    color: var(--paper); font-size: 15px; font-weight: 400;
  }
  .address-rule {
    position: absolute; left: 0; bottom: 90px; width: 520px; height: 3px;
    background: var(--green);
  }
  .band-square {
    position: absolute; left: 540px; bottom: 44px; width: 38px; height: 38px;
    background: var(--ink);
  }
  .band-tail {
    position: absolute; left: 598px; right: 0; bottom: 44px; height: 38px;
    background: var(--green);
  }
</style>
</head>
<body>
<main class="sheet">

  <section class="card card--front" aria-label="Card front">
    <div class="front-mark">
      <span class="front-mark__square"></span>
      <p class="front-mark__name"><span class="line1">Ridgeline</span><span class="line2">Design + Build</span></p>
    </div>
  </section>

  <section class="card card--back" aria-label="Card back">
    <p class="back-brand"><span class="line1">Ridgeline</span><span class="line2">Design + Build</span></p>
    <span class="divider"></span>

    <div class="contact">
      <h1 class="contact__name">Maren Holt</h1>
      <p class="contact__title">Owner-CEO</p>
      <ul class="contact__list">
        <li>
          <svg viewBox="0 0 24 24" aria-hidden="true"><path d="M6.6 10.8a15.2 15.2 0 0 0 6.6 6.6l2.2-2.2c.3-.3.7-.4 1-.2 1.1.4 2.3.6 3.6.6.6 0 1 .4 1 1V20c0 .6-.4 1-1 1A17 17 0 0 1 3 4c0-.6.4-1 1-1h3.5c.6 0 1 .4 1 1 0 1.3.2 2.5.6 3.6.1.3 0 .7-.2 1z"/></svg>
          123 456 789
        </li>
        <li>
          <svg viewBox="0 0 24 24" aria-hidden="true"><path d="M7 1h10a2 2 0 0 1 2 2v18a2 2 0 0 1-2 2H7a2 2 0 0 1-2-2V3a2 2 0 0 1 2-2zm0 3v14h10V4zm5 15.2a1.2 1.2 0 1 0 0 2.4 1.2 1.2 0 0 0 0-2.4z"/></svg>
          123 456 789
        </li>
        <li>
          <svg viewBox="0 0 24 24" aria-hidden="true"><path d="M2 5h20v14H2zm2 2v.4l8 5.2 8-5.2V7zm0 2.8V17h16V9.8l-8 5.2z"/></svg>
          info@yourgmail.com
        </li>
        <li>
          <svg viewBox="0 0 24 24" aria-hidden="true"><path d="M12 2a10 10 0 1 0 0 20 10 10 0 0 0 0-20zm6.9 9h-3a15 15 0 0 0-1.3-6A8 8 0 0 1 18.9 11zM12 4.1c.9 1.4 1.7 3.7 1.9 6.9h-3.8c.2-3.2 1-5.5 1.9-6.9zM9.4 5a15 15 0 0 0-1.3 6h-3A8 8 0 0 1 9.4 5zM5.1 13h3a15 15 0 0 0 1.3 6 8 8 0 0 1-4.3-6zm6.9 6.9c-.9-1.4-1.7-3.7-1.9-6.9h3.8c-.2 3.2-1 5.5-1.9 6.9zm2.6-.9a15 15 0 0 0 1.3-6h3a8 8 0 0 1-4.3 6z"/></svg>
          www.yourwebsite.com
        </li>
      </ul>
    </div>

    <span class="address-rule"></span>
    <p class="address-band">Your address, City State, Zip 1234</p>
    <span class="band-square"></span>
    <span class="band-tail"></span>
  </section>

</main>
</body>
</html>
```